Website for Scientific & Engineering Organization

Overview

The objective is to design a professional, easy-to-navigate, and visually appealing website for the <Enclosed Organization (see attached files)>, reflecting their esteemed status in the engineering and scientific community.

Pages:

Home (About Us) : Introduce the organization, highlighting their activities, history, and fellowship. Include a section for latest news highlights.

News and Programme : Dedicated page for news updates and detailed annual programmes

Gallery : This page will feature photographs and descriptions of the society's 'Voyages' and events.

Downloads : A section offering downloadable content such as newsletters and lecture materials, organized for user-friendliness.

Members Section : A private area for members to access exclusive content. Alternatively, a 'Membership' page with joining details and benefits if more public-facing content is preferred.

Design Elements:

Layout : A linear layout with a fixed top navigation bar for easy movement between pages.
Color Scheme : Utilize the provided colors (#395394, #E00053, #0043E1) to create a cohesive and professional aesthetic.
Typography : Use a combination of serif for headings and sans-serif for body text, ensuring readability and elegance.

Features:

Responsive Design : The design will accommodate various devices, ensuring consistency across mobiles, tablets, and desktops.

Accessibility : Design for all users with adequate spacing around elements and color contrasts

Content Strategy (Visual Focus):

Home Page : Visual emphasis on the introduction, mission, and recent 'Voyages' with engaging imagery and concise text.
News and Programme : Clear, visually distinct sections for news and the annual schedule
Gallery : A visually rich page with a grid or album layout, allowing users to easily browse through the years and events.
Downloads : Neatly organized sections with clear labels and icons to represent the different types of available downloads. Downloads are PDF newsletter/flyers/programmes etc...
Members Section/Membership : A design that conveys exclusivity and value, encouraging sign-ups and engagement from members.
Design Considerations:

Consistency : Ensure the design reflects the organization's heritage and professionalism throughout all pages.
User Experience : Focus on intuitive navigation and information architecture to guide visitors smoothly through the site.
Visual Hierarchy : Use size, color, and layout to emphasize key areas and direct user attention effectively.
Final Notes:

This design spec focuses on creating a web presence that mirrors the organization's prestige and heritage, providing an engaging, informative platform for members and the public alike. The design will be crafted to allow for easy content updates and adaptability, ensuring a long-lasting and effective website.

Target Market(s)

Non profit science and engineering. Older people

Industry/Entity Type

Non profit scientific organization

Number of Pages Required

5+ page

Requirements
Should not have
• No search feature

```html
<!DOCTYPE html>
<html lang="en">
<head>
<meta charset="utf-8">
<title>SFSI British Section</title>
<link rel="stylesheet" href="https://fonts.googleapis.com/css2?family=Playfair+Display:wght@400;500;600&family=Roboto:wght@400;500;700&display=swap">
<style>
:root{
  --navy:#395394;
  --pink:#c8236b;
  --pink-strong:#e00053;
  --blue:#0043e1;
  --ink:#1b1b1b;
  --body:#333;
  --muted:#666;
  --blush:#f8e9f1;
  --lilac:#eceaf7;
  --card-grey:#f3f3f3;
  --black:#000;
  --white:#fff;
}
*{box-sizing:border-box;margin:0;padding:0}
html,body{width:1200px;height:4188px;overflow:hidden}
body{position:relative;background:var(--white);font-family:'Roboto',sans-serif;color:var(--body)}
.abs{position:absolute}
.accent{color:var(--pink)}
.btn{position:absolute;display:flex;align-items:center;gap:6px;background:var(--blue);color:var(--white);font:700 17px 'Roboto',sans-serif;border-radius:24px;padding:0 26px;height:44px}
.btn svg{width:15px;height:15px}
.btn-white{background:var(--white);color:var(--ink)}
.rule{position:absolute;height:2px;background:var(--ink);width:110px}

/* header */
.site-header{position:absolute;top:0;left:0;width:1200px;height:100px;background:var(--white)}
.brand{position:absolute;left:125px;top:20px;display:flex;align-items:center;gap:12px}
.brand-mark{width:54px;height:54px;border-radius:50%;background:var(--navy)}
.brand-name{font:700 34px 'Roboto',sans-serif;color:var(--blue);letter-spacing:1px}
.nav{position:absolute;display:flex;gap:16px;font-size:14px;color:var(--ink)}
.nav .dd::after{content:"";display:inline-block;margin-left:4px;border:4px solid transparent;border-top:5px solid currentColor;vertical-align:-1px}
.header-nav{left:366px;top:33px}
.contact-btn{left:919px;top:20px;height:44px;font-size:18px}

/* hero */
.hero-text .welcome{left:120px;top:184px;font-size:19px;color:var(--ink)}
.hero-text h1{left:120px;top:222px;font:500 46px/60px 'Playfair Display',serif;color:var(--ink)}
.hero-text .tag{left:120px;top:355px;font-size:23px;font-weight:500;color:var(--ink)}

/* features */
.welcome-box{left:112px;top:800px;width:316px;height:316px;background:var(--blue);color:var(--white)}
.welcome-box h2{position:absolute;left:33px;top:40px;font:500 33px/41px 'Roboto',sans-serif}
.feature{text-align:center}
.feature h3{font:500 18px 'Roboto',sans-serif;color:var(--ink);margin:14px 0 12px}
.feature p{font-size:14px;line-height:23px;color:var(--muted);width:210px;margin:0 auto}
.feature-plain{left:468px;top:800px;width:292px;height:301px;background:var(--card-grey);padding:44px 24px}
.feature-raised{left:797px;top:813px;width:291px;height:301px;background:var(--white);box-shadow:0 2px 10px rgba(0,0,0,.18);padding:40px 26px}

/* section headings */
.sec-title{font:500 42px 'Playfair Display',serif;color:var(--ink)}

/* about */
.tab{position:absolute;top:1366px;height:37px;border-radius:19px;background:var(--blue);color:var(--white);font:700 14px 'Roboto',sans-serif;display:flex;align-items:center;justify-content:center}
.tab.active{background:var(--pink)}
.activity-head{left:112px;top:1488px;display:flex;align-items:center;gap:12px;font:700 20px 'Roboto',sans-serif;color:var(--ink)}
.icon-ring{width:55px;height:55px;border-radius:50%;border:3px solid #ddd;background:var(--white);display:flex;align-items:center;justify-content:center}
.about-copy{left:112px;top:1560px;width:390px;font-size:14px;line-height:23px;color:var(--ink)}

/* news */
.news-card{position:absolute;top:2119px;width:287px}
.news-photo{width:287px;height:219px}
.news-date{margin-top:30px;font-size:13.5px;color:var(--muted);display:flex;align-items:center;gap:5px}
.news-title{margin-top:8px;font:500 17px/26px 'Roboto',sans-serif;color:var(--ink);height:54px}
.news-sub{margin-top:6px;font-size:13.5px;line-height:21px;color:var(--ink);text-transform:uppercase;font-weight:500;height:42px;width:250px}
.news-more{margin-top:8px;font-size:13.5px;color:var(--pink);text-decoration:underline;font-weight:500}
.arrow-btn{position:absolute;width:32px;height:32px;border-radius:50%;display:flex;align-items:center;justify-content:center}

/* members */
.members-copy{font-size:14.5px;line-height:23px;color:var(--ink)}
.members-copy a{color:var(--blue);font-weight:500}

/* newsletter */
.newsletter-panel{position:absolute;left:132px;top:3608px;width:938px;height:229px;background:var(--pink)}
.newsletter h2{position:absolute;left:183px;top:3655px;font:500 38px 'Playfair Display',serif;color:var(--white)}
.email-field{position:absolute;left:175px;top:3727px;width:460px;height:40px;border-radius:20px;background:var(--white);font-size:13.5px;color:var(--muted);padding:12px 30px}
.email-field .sub-btn{position:absolute;right:3px;top:3px;height:34px;width:145px;border-radius:17px;background:var(--blue);color:var(--white);font:700 17px 'Roboto',sans-serif;display:flex;align-items:center;justify-content:center}
.news-note{left:729px;top:3662px;width:270px;font-size:14px;line-height:24px;color:var(--white)}
.news-note u{font-weight:500}

/* footer */
.site-footer{position:absolute;left:0;top:3837px;width:1200px;height:351px;background:var(--black);color:var(--white);text-align:center}
.footer-brand{position:absolute;left:0;width:1200px;top:70px;display:flex;justify-content:center;align-items:center;gap:14px}
.footer-mark{width:60px;height:60px;border-radius:50%;border:3px solid var(--white)}
.footer-name{font:700 28px 'Roboto',sans-serif}
.site-footer .tagline{position:absolute;left:0;width:1200px;top:168px;font-size:14.5px}
.footer-nav{left:307px;top:229px;color:var(--white);font-size:14.5px}
.copyright{position:absolute;left:0;width:1200px;top:285px;font-size:12px}
</style>
</head>
<body>

<header class="site-header">
  <div class="brand"><span class="brand-mark"></span><span class="brand-name">SFSI</span></div>
  <nav class="nav header-nav">
    <span class="dd">About Us</span><span class="dd">News &amp; Programme</span><span>Gallery</span><span class="dd">Downloads</span><span class="dd">Members Section</span>
  </nav>
  <span class="btn contact-btn">Contact Us <svg viewBox="0 0 16 16"><circle cx="8" cy="8" r="8" fill="currentColor"/><path d="M6.5 4.5 10 8l-3.5 3.5" stroke="#0043e1" stroke-width="2.2" fill="none"/></svg></span>
</header>

<svg class="abs" style="left:0;top:100px" width="1200" height="620" viewBox="0 0 1200 620">
  <defs>
    <linearGradient id="heroSky" x1="0" y1="0" x2="1" y2="1">
      <stop offset="0" stop-color="#ffffff"/>
      <stop offset=".35" stop-color="#d9e6f2"/>
      <stop offset=".7" stop-color="#a9bfd6"/>
      <stop offset="1" stop-color="#8a9a6a"/>
    </linearGradient>
  </defs>
  <path role="img" aria-label="Photo of smiling members in front of a Paris landmark" d="M420 0H1200V450L840 595 180 490C300 430 380 300 420 0Z" fill="url(#heroSky)"/>
  <path d="M175 488 840 612 1200 460V430L840 580 175 488Z" fill="var(--pink)"/>
</svg>
<div class="hero-text">
  <p class="abs welcome">Welcome To</p>
  <h1 class="abs">The British Section Of<br>The SFSI</h1>
  <p class="abs tag">Sharing Knowledge and a Love of France</p>
</div>
<span class="btn" style="left:120px;top:411px">Get Started <svg viewBox="0 0 16 16"><circle cx="8" cy="8" r="8" fill="currentColor"/><path d="M6.5 4.5 10 8l-3.5 3.5" stroke="#0043e1" stroke-width="2.2" fill="none"/></svg></span>

<div class="abs welcome-box">
  <h2>NEW MEMBERS<br>ARE<br>ALWAYS<br>WELCOME</h2>
  <span class="btn btn-white" style="left:33px;top:224px">Learn More <svg viewBox="0 0 16 16"><circle cx="8" cy="8" r="8" fill="#1b1b1b"/><path d="M6.5 4.5 10 8l-3.5 3.5" stroke="#fff" stroke-width="2.2" fill="none"/></svg></span>
</div>
<div class="abs feature feature-plain">
  <svg width="48" height="48" viewBox="0 0 48 48"><circle cx="24" cy="24" r="24" fill="var(--blue)"/><path d="M24 11l3.8 8.2 8.9 1-6.6 6 1.9 8.8L24 30.5 16 35l1.9-8.8-6.6-6 8.9-1Z" fill="#fff"/></svg>
  <h3>Equal Importance</h3>
  <p>An informal society of engineers and scientists, giving equal importanceto the quality of our technical activities and our fellowship.</p>
</div>
<div class="abs feature feature-raised">
  <svg width="44" height="52" viewBox="0 0 44 52"><circle cx="22" cy="7" r="6" fill="var(--blue)"/><rect x="12" y="16" width="20" height="8" rx="3" fill="var(--blue)"/><rect x="2" y="26" width="40" height="6" fill="var(--blue)"/><path d="M8 34h28l-4 16H12Z" fill="var(--blue)"/></svg>
  <h3>Quality Lecture</h3>
  <p>We provide high quality lectures and technical visits on diverse engineering and scientific subjects, and the enjoyment of French</p>
</div>

<svg class="abs" style="left:0;top:1200px" width="1200" height="750" viewBox="0 0 1200 750">
  <defs>
    <linearGradient id="band" x1="0" y1="0" x2="0" y2="1">
      <stop offset="0" stop-color="var(--blush)"/><stop offset="1" stop-color="var(--lilac)"/>
    </linearGradient>
  </defs>
  <path d="M0 150 358 30 1200 150V610L840 745 0 610Z" fill="url(#band)"/>
  <path d="M80 117 358 6 1010 117 370 32Z" fill="var(--pink)"/>
  <path d="M160 630 840 745 1120 630 840 725Z" fill="var(--pink)"/>
</svg>
<h2 class="abs sec-title" style="left:112px;top:1378px"><span class="accent">About</span> Us</h2>
<span class="rule" style="left:112px;top:1445px"></span>
<span class="tab" style="left:542px;width:124px">Introduction</span>
<span class="tab active" style="left:682px;width:124px">Our Activities</span>
<span class="tab" style="left:822px;width:124px">History</span>
<span class="tab" style="left:962px;width:124px">FellowShip</span>
<div class="abs activity-head"><span class="icon-ring"><svg width="24" height="24" viewBox="0 0 24 24"><rect x="2" y="2" width="20" height="20" rx="4" fill="var(--pink)"/><circle cx="12" cy="12" r="5" fill="none" stroke="#fff" stroke-width="2"/><circle cx="12" cy="12" r="1.6" fill="#fff"/></svg></span>Our Activities</div>
<p class="abs about-copy">Five or six high quality technical lectures are arranged throughout the year at a number of London venues followed by dinner. Memorable lectures have includedtopics as diverse as the building of the Panama Canal, the origins of SI standardmeasurements and the current Antarctic research programme.</p>
<span class="btn" style="left:112px;top:1728px">Learn More <svg viewBox="0 0 16 16"><circle cx="8" cy="8" r="8" fill="currentColor"/><path d="M6.5 4.5 10 8l-3.5 3.5" stroke="#0043e1" stroke-width="2.2" fill="none"/></svg></span>
<svg class="abs" style="left:595px;top:1440px" width="420" height="430" viewBox="0 0 420 430">
  <defs>
    <linearGradient id="hexRim" x1="0" y1="0" x2="1" y2="0"><stop offset="0" stop-color="var(--pink)"/><stop offset="1" stop-color="var(--blue)"/></linearGradient>
    <linearGradient id="hexFill" x1="0" y1="0" x2="0" y2="1"><stop offset="0" stop-color="#c9d6e3"/><stop offset="1" stop-color="#1f3550"/></linearGradient>
  </defs>
  <path d="M90 40 285 8 415 165 378 388 200 425 30 330 0 210Z" fill="url(#hexRim)"/>
  <path role="img" aria-label="Photo of a speaker presenting to a seated audience" d="M98 52 280 22 402 168 366 378 200 412 42 322 14 210Z" fill="url(#hexFill)"/>
</svg>

<h2 class="abs sec-title" style="left:0;width:1200px;text-align:center;top:2008px"><span class="accent">News</span> and Programme</h2>
<span class="rule" style="left:545px;top:2074px"></span>
<span class="arrow-btn" style="left:70px;top:2235px;background:#8fa8f2"><svg width="10" height="10" viewBox="0 0 10 10"><path d="M6.5 1.5 3 5l3.5 3.5" stroke="#fff" stroke-width="1.8" fill="none"/></svg></span>
<span class="arrow-btn" style="left:1099px;top:2242px;background:var(--blue)"><svg width="10" height="10" viewBox="0 0 10 10"><path d="M3.5 1.5 7 5 3.5 8.5" stroke="#fff" stroke-width="1.8" fill="none"/></svg></span>

<article class="news-card" style="left:112px">
  <div class="news-photo" role="img" aria-label="Photo of guests at a formal dinner" style="background:linear-gradient(160deg,#c9b49a,#7a6a5c 60%,#d9d4cd)"></div>
  <p class="news-date"><svg width="14" height="14" viewBox="0 0 14 14"><rect x="1" y="2" width="12" height="11" fill="none" stroke="var(--blue)" stroke-width="1.4"/><path d="M1 5h12M4 1v3M10 1v3M4 8h2M8 8h2M4 10h2M8 10h2" stroke="var(--blue)" stroke-width="1.2"/></svg>29 January 2024</p>
  <h3 class="news-title">Incoming President's Inaugural lecture and dinner</h3>
  <p class="news-sub" style="width:287px">Forensic Fire Investigation:<br><span style="font-weight:400">The underpinning fire science and</span></p>
  <p class="news-more">View More</p>
</article>
<article class="news-card" style="left:467px">
  <div class="news-photo" role="img" aria-label="Photo of an audience in a lecture hall" style="background:linear-gradient(170deg,#e8d9c8,#b5714e 55%,#5a3a2c)"></div>
  <p class="news-date"><svg width="14" height="14" viewBox="0 0 14 14"><rect x="1" y="2" width="12" height="11" fill="none" stroke="var(--blue)" stroke-width="1.4"/><path d="M1 5h12M4 1v3M10 1v3M4 8h2M8 8h2M4 10h2M8 10h2" stroke="var(--blue)" stroke-width="1.2"/></svg>29 January 2024</p>
  <h3 class="news-title">Evening Lecture and Dinner</h3>
  <p class="news-sub">How to protect people and homes from wildfires:</p>
  <p class="news-more">View More</p>
</article>
<article class="news-card" style="left:823px">
  <div class="news-photo" role="img" aria-label="Photo of a buffet table with guests" style="background:linear-gradient(170deg,#d8d2cc,#8a7f78 45%,#b8894a 80%,#6b8a3a)"></div>
  <p class="news-date"><svg width="14" height="14" viewBox="0 0 14 14"><rect x="1" y="2" width="12" height="11" fill="none" stroke="var(--blue)" stroke-width="1.4"/><path d="M1 5h12M4 1v3M10 1v3M4 8h2M8 8h2M4 10h2M8 10h2" stroke="var(--blue)" stroke-width="1.2"/></svg>29 January 2024</p>
  <h3 class="news-title">Evening Lecture and Dinner</h3>
  <p class="news-sub">Unplanned adventures in fire science, engineering, and</p>
  <p class="news-more">View More</p>
</article>

<svg class="abs" style="left:0;top:2585px" width="1200" height="670" viewBox="0 0 1200 670">
  <path d="M0 130 358 20 1200 130V550L840 665 0 550Z" fill="url(#band)"/>
  <path d="M80 100 358 0 1010 100 370 22Z" fill="var(--pink)"/>
  <path d="M160 560 840 665 1120 560 840 645Z" fill="var(--pink)"/>
</svg>
<h2 class="abs sec-title" style="left:0;width:1200px;text-align:center;top:2692px"><span class="accent">Our</span> Gallery</h2>
<span class="rule" style="left:545px;top:2758px"></span>
<div class="abs" role="img" aria-label="Photo of an engineer in a tunnel" style="left:0;top:2811px;width:172px;height:246px;background:linear-gradient(150deg,#8a8a82,#d8d8d0 50%,#e6c21a 80%)"></div>
<div class="abs" role="img" aria-label="Photo of members dining in a hall" style="left:197px;top:2811px;width:253px;height:246px;background:linear-gradient(170deg,#c9a57a,#8a4d3a 60%,#e0d6cc)"></div>
<div class="abs" role="img" aria-label="Photo of a group of members on a visit" style="left:473px;top:2811px;width:255px;height:246px;background:linear-gradient(170deg,#8c9488,#6d6a62 50%,#b9b2aa)"></div>
<div class="abs" role="img" aria-label="Photo of a member speaking at a microphone" style="left:751px;top:2811px;width:254px;height:246px;background:linear-gradient(160deg,#6a4a3a,#3a2a24 55%,#b9b2c8)"></div>
<div class="abs" role="img" aria-label="Photo of a river estuary view" style="left:1028px;top:2811px;width:172px;height:246px;background:linear-gradient(180deg,#c8ccd0,#9aa0a4 45%,#5a6450 70%,#8a9aa8)"></div>
<span class="arrow-btn" style="left:70px;top:2919px;background:#4a6fd8"><svg width="10" height="10" viewBox="0 0 10 10"><path d="M6.5 1.5 3 5l3.5 3.5" stroke="#fff" stroke-width="1.8" fill="none"/></svg></span>
<span class="arrow-btn" style="left:1099px;top:2919px;background:var(--blue)"><svg width="10" height="10" viewBox="0 0 10 10"><path d="M3.5 1.5 7 5 3.5 8.5" stroke="#fff" stroke-width="1.8" fill="none"/></svg></span>

<h2 class="abs sec-title" style="left:112px;top:3273px"><span class="accent">Our</span> Members</h2>
<span class="rule" style="left:112px;top:3340px"></span>
<p class="abs members-copy" style="left:114px;top:3370px;width:460px">The origins of the Section lie in civil engineering.&nbsp; For many years, however, in line with the now named Société Franco-Savante d'Ingénierie (SFSI), we have been open to membership from like minded people from all fields of engineering and science. We are always delighted to welcome new members.</p>
<div class="abs members-copy" style="left:636px;top:3370px;width:460px">
  <p>If you would like to join us or would like further information on membership,</p>
  <p style="margin-top:12px">please click <a style="text-decoration:underline">Membership</a></p>
  <p style="margin-top:12px">contact an existing member, or the Membership Secretary, Tom Hartley, <a style="text-decoration:underline">t.hartley@examplemail.co.uk</a></p>
</div>
<span class="btn" style="left:114px;top:3496px">Learn More <svg viewBox="0 0 16 16"><circle cx="8" cy="8" r="8" fill="currentColor"/><path d="M6.5 4.5 10 8l-3.5 3.5" stroke="#0043e1" stroke-width="2.2" fill="none"/></svg></span>

<section class="newsletter">
  <div class="newsletter-panel"></div>
  <svg class="abs" style="left:132px;top:3608px" width="938" height="229" viewBox="0 0 938 229">
    <path d="M535 20C565 70 565 165 535 215" stroke="#fff" stroke-width="2" fill="none"/>
  </svg>
  <h2>Subcribe To Our Newsletter</h2>
  <div class="email-field">Enter Email Address<span class="sub-btn">Subscribe</span></div>
  <p class="abs news-note">The Society for Engineers and Scientists where they sample French cuisine and culture with their partners as well as continue their professional interests<br><u style="display:inline-block;margin-top:4px">Download News And Materials</u></p>
</section>

<footer class="site-footer">
  <div class="footer-brand"><span class="footer-mark"></span><span class="footer-name">SFSI</span></div>
  <p class="tagline">Sharing Knowledge and a Love of France</p>
  <nav class="nav footer-nav">
    <span class="dd">About Us</span><span class="dd">News &amp; Programme</span><span>Gallery</span><span class="dd">Downloads</span><span class="dd">Members Section</span><span>Contact</span>
  </nav>
  <p class="copyright">Copyright@2024. All Rights Reserved By SFSI</p>
</footer>

</body>
</html>
```